Stationery Set for Velmora Company

I need to create full stationery design for my company; Business Cards, Envelops, Letter Heads, Calendar.
In the letter head and Envelops... only contact information and website links.
Our company is a Service Management company with different domains of innovative services including Technology Service Management, Education Services, Outsourcing Management, Events Management.
I need a modern and innovative design specially for the business card. I some transparent designs and I like it, but don't limit your innovation to what I mentioned. Sky is limit for your innovation.

Target Market(s)

Middle East & Africa

Industry/Entity Type

Business Management

Colors
34a7d8
0355a3
85acd3
86cae7
cee9f5
cfdeed
e4daeb
f3f1f8
ecf7fb

Requirements
Must have
• Name, Title, Email, Mobile
Nice to have
• We have multiple locations in USA, KSA, EGY, so I need ideas about how to include all contact details maybe QR / Barcode or something else.
• Please see our locations and contact information: www.brightvelmora.example
Should not have
• Too much text

```html
<!DOCTYPE html>
<html lang="en">
<head>
<meta charset="utf-8">
<title>Velmora Company — Business Card</title>
<link rel="stylesheet" href="https://fonts.googleapis.com/css2?family=Fira+Sans:wght@400;500;600;700&display=swap">
<style>
  :root {
    --backdrop: #909293;
    --card: #eeeff1;
    --brand-blue: #3159a3;
    --ink: #1c1c1c;
    --on-blue: #ffffff;
    --pattern-tint: #d3dbe8;
  }
  * { margin: 0; padding: 0; box-sizing: border-box; }
  html, body { width: 1105px; height: 1200px; overflow: hidden; }
  body {
    background: var(--backdrop);
    font-family: "Fira Sans", Arial, sans-serif;
    position: relative;
  }
  .card {
    position: absolute;
    left: 182px;
    width: 746px;
    height: 427px;
    background: var(--card);
    overflow: hidden;
  }
  .card--front { top: 119px; }
  .card--back { top: 637px; }

  .blue-panel { position: absolute; inset: 0; }

  .contact {
    position: absolute;
    left: 55px;
    top: 58px;
    color: var(--on-blue);
    font-size: 19px;
    line-height: 26px;
  }
  .contact-group { margin-bottom: 10px; }
  .contact-line { display: flex; align-items: center; gap: 12px; }
  .contact-line svg { width: 18px; height: 18px; flex: none; }

  .brand {
    position: absolute;
    display: flex;
    align-items: center;
    gap: 10px;
    color: var(--brand-blue);
    font-weight: 600;
    font-size: 30px;
    white-space: nowrap;
  }
  .brand-dot {
    width: 16px; height: 16px;
    border-radius: 50%;
    background: var(--brand-blue);
  }
  .card--front .brand { left: 420px; top: 136px; }
  .card--back .brand { left: 418px; top: 246px; }

  .holder {
    position: absolute;
    left: 420px;
    width: 260px;
    top: 262px;
    text-align: center;
  }
  .holder-name {
    color: var(--brand-blue);
    font-weight: 600;
    font-size: 25px;
    letter-spacing: 0.5px;
  }
  .holder-title {
    color: var(--ink);
    font-size: 19px;
    margin-top: 2px;
  }

  .pattern-area { position: absolute; inset: 0; }

  .website {
    position: absolute;
    left: 412px;
    top: 358px;
    color: var(--ink);
    font-size: 21px;
    font-weight: 500;
    letter-spacing: 1.5px;
  }
</style>
</head>
<body>

  <section class="card card--front">
    <svg class="blue-panel" width="746" height="427" viewBox="0 0 746 427" aria-hidden="true">
      <path d="M0 0 H372 C330 20 300 80 318 160 C336 240 380 320 385 427 H0 Z" fill="var(--brand-blue)"/>
    </svg>

    <div class="contact">
      <div class="contact-group">
        <div>418 Maple Crest Avenue</div>
        <div>4th Floor Fairview City</div>
        <div>CA 90210 US</div>
        <div class="contact-line">
          <svg viewBox="0 0 24 24" aria-hidden="true"><path fill="currentColor" d="M6.6 10.8a15 15 0 0 0 6.6 6.6l2.2-2.2a1 1 0 0 1 1-.25 11.4 11.4 0 0 0 3.6.57 1 1 0 0 1 1 1V20a1 1 0 0 1-1 1A17 17 0 0 1 3 4a1 1 0 0 1 1-1h3.5a1 1 0 0 1 1 1c0 1.25.2 2.45.57 3.57a1 1 0 0 1-.25 1z"/></svg>
          <span>+1.5550148822</span>
        </div>
      </div>
      <div class="contact-group">
        <div>Riyadh, Al Nakheel,</div>
        <div>Qasr Garden St.</div>
        <div>Noor Plaza Buildings</div>
        <div>Block 4C 3rd Floor C12, C14</div>
        <div class="contact-line">
          <svg viewBox="0 0 24 24" aria-hidden="true"><path fill="currentColor" d="M6.6 10.8a15 15 0 0 0 6.6 6.6l2.2-2.2a1 1 0 0 1 1-.25 11.4 11.4 0 0 0 3.6.57 1 1 0 0 1 1 1V20a1 1 0 0 1-1 1A17 17 0 0 1 3 4a1 1 0 0 1 1-1h3.5a1 1 0 0 1 1 1c0 1.25.2 2.45.57 3.57a1 1 0 0 1-.25 1z"/></svg>
          <span>+966 90000 11 37</span>
        </div>
      </div>
      <div class="contact-group">
        <div class="contact-line">
          <svg viewBox="0 0 24 24" aria-hidden="true"><rect x="6" y="2" width="12" height="20" rx="2" fill="none" stroke="currentColor" stroke-width="2"/><circle cx="12" cy="18" r="1.2" fill="currentColor"/></svg>
          <span>+1.5550148822</span>
        </div>
        <div class="contact-line">
          <svg viewBox="0 0 24 24" aria-hidden="true"><rect x="2" y="5" width="20" height="14" rx="1.5" fill="currentColor"/><path d="M3 6l9 7 9-7" fill="none" stroke="var(--brand-blue)" stroke-width="1.6"/></svg>
          <span>info@brightvelmora.example</span>
        </div>
      </div>
    </div>

    <div class="brand"><span class="brand-dot"></span><span>Velmora Company</span></div>

    <div class="holder">
      <div class="holder-name">DANIEL HARLOW</div>
      <div class="holder-title">CEO/Founder</div>
    </div>
  </section>

  <section class="card card--back">
    <svg class="pattern-area" width="746" height="427" viewBox="0 0 746 427" role="img" aria-label="Faint repeating pattern of outlined light bulbs across the card">
      <defs>
        <linearGradient id="pattern-fade" x1="0" y1="0" x2="1" y2="1">
          <stop offset="0" stop-color="var(--pattern-tint)"/>
          <stop offset="0.6" stop-color="var(--card)"/>
        </linearGradient>
      </defs>
      <rect width="746" height="427" fill="url(#pattern-fade)"/>
    </svg>

    <div class="brand"><span class="brand-dot"></span><span>Velmora Company</span></div>
    <div class="website">www.brightvelmora.example</div>
  </section>

</body>
</html>
```